Email Preference Page Design

We are looking for a 2 page design for our users to edit their email preferences and submit friend referrals. You can find the fuctionality, content and text here:

https://brightvanta.mailrelayhub.example/app/linkClick/7281/5fa9c1d3b07e442b/28374615/9bd4e01a7c3f2a65

* the shipping and billing address might be different so you need to show the billing if the "same as shipping" box is not checked. It can auto-hide like the page above shows if that fits your design.

* when the "unsubscribe from all email lists" box is selected, all the other checkbox options will hide as in the example page. We need you to show us what the site will look like with and without that checkbox selected.

We want to match these two pages to the general feel of these website pages:

www.brightvanta.com
and
free.brightvanta.com

The page should be very clean and tight. Project is for design only but must be able to be implemented in html showing button and checkbox states. Technically this must be two pages for our system - one for all the user info and one for individual email referrals (see example above).

Target Market(s)

video professionals

Industry/Entity Type

Shipping

Requirements
Must have
• our logo (see numerous versions attached)
well designed header
well designed sections
clean editable text
tight layout
html friendly
easy to understand
2 pages
Nice to have
• custom checkboxes and radio buttons

```html
<!DOCTYPE html>
<html lang="en">
<head>
<meta charset="utf-8">
<title>BrightVanta — Communication Preferences</title>
<link rel="stylesheet" href="https://fonts.googleapis.com/css2?family=Barlow+Semi+Condensed:wght@500&family=Source+Sans+3:wght@300;400&display=swap">
<style>
  :root {
    --navy: #1c3142;
    --page: #efefef;
    --panel: #ffffff;
    --orange: #f05a1e;
    --orange-light: #fb7d3a;
    --ink: #25323c;
    --muted: #6b6f73;
    --field: #f4f4f4;
    --field-line: #cfcfcf;
  }
  * { box-sizing: border-box; margin: 0; padding: 0; }
  html, body { width: 979px; height: 1200px; overflow: hidden; }
  body {
    position: relative;
    background: var(--page);
    font-family: "Source Sans 3", sans-serif;
    color: var(--ink);
  }
  .top-band { position: absolute; left: 0; top: 0; width: 979px; height: 61px; background: var(--navy); }
  .brand-tab { position: absolute; left: 258px; top: 0; width: 463px; height: 112px; }
  .brand-name {
    position: absolute; left: 258px; top: 14px; width: 463px;
    display: flex; align-items: center; justify-content: center; gap: 12px;
    font-size: 44px; font-weight: 400; color: #2b2b2b; letter-spacing: 0.5px;
  }
  .brand-dot { width: 26px; height: 26px; border-radius: 50%; background: var(--orange); }
  .page-title {
    position: absolute; left: 65px; top: 138px;
    font-family: "Barlow Semi Condensed", sans-serif; font-weight: 500;
    font-size: 36px; color: var(--orange); letter-spacing: 1px;
  }
  .panel { position: absolute; left: 60px; width: 856px; background: var(--panel); border-radius: 4px; box-shadow: 0 0 2px rgba(0,0,0,.06); }
  .panel-contact { top: 194px; height: 378px; }
  .panel-filter { top: 597px; height: 494px; }
  .section-title { position: absolute; font-weight: 400; color: var(--ink); }
  .field {
    position: absolute; height: 30px; background: var(--field);
    border: 1px solid var(--field-line); border-radius: 3px;
    font-size: 12.5px; color: var(--muted); padding: 6px 14px; font-weight: 400;
  }
  .plus { position: absolute; font-size: 14px; color: var(--ink); }
  .check { position: absolute; display: flex; align-items: center; gap: 8px; font-size: 11px; color: var(--muted); white-space: nowrap; }
  .box { width: 15px; height: 15px; border: 1px solid #c8c8c8; border-radius: 3px; background: #fafafa; flex: none; }
  .check.large { font-size: 11.5px; gap: 10px; }
  .check.large .box { width: 18px; height: 18px; }
  .group-title { position: absolute; left: 43px; font-size: 14.5px; color: var(--orange); }
  .submit {
    position: absolute; left: 44px; top: 412px; width: 110px; height: 36px;
    border: 1px solid #d8481a; border-radius: 2px;
    background: linear-gradient(#fb8a48, var(--orange));
    color: #fff; font-size: 18px; font-family: inherit;
  }
  .footer { position: absolute; left: 0; top: 1125px; width: 979px; height: 75px; background: var(--navy); }
  .footer p { text-align: center; margin-top: 28px; font-size: 10.5px; color: #e2e6ea; font-weight: 300; }
</style>
</head>
<body>
  <header>
    <div class="top-band"></div>
    <svg class="brand-tab" viewBox="0 0 463 112" aria-hidden="true">
      <path d="M0 0 H463 V88 Q231 128 0 88 Z" fill="#ffffff"/>
    </svg>
    <div class="brand-name"><span class="brand-dot"></span>brightvanta</div>
  </header>

  <h1 class="page-title">Communication Preferences</h1>

  <section class="panel panel-contact">
    <h2 class="section-title" style="left:34px;top:27px;font-size:22px;">Contact Information</h2>
    <div class="field" style="left:34px;top:63px;width:255px;">First Name</div>
    <div class="field" style="left:300px;top:63px;width:255px;">Last Name</div>
    <div class="field" style="left:569px;top:63px;width:255px;">Email address</div>
    <div class="field" style="left:34px;top:103px;width:255px;">Phone no.</div>
    <div class="field" style="left:300px;top:103px;width:255px;">Address</div>
    <div class="field" style="left:569px;top:103px;width:255px;">Address 2</div>
    <div class="field" style="left:34px;top:144px;width:255px;">Address 3</div>
    <div class="field" style="left:300px;top:144px;width:255px;">City</div>
    <div class="field" style="left:569px;top:144px;width:255px;">Country</div>
    <div class="field" style="left:34px;top:184px;width:255px;">State</div>
    <div class="field" style="left:300px;top:184px;width:160px;">Postal Code + 4</div>
    <span class="plus" style="left:466px;top:189px;">+</span>
    <div class="field" style="left:483px;top:184px;width:72px;"></div>
    <label class="check large" style="left:37px;top:234px;"><span class="box"></span>Subscribe me to your general email list&nbsp; This monthly email includes free video loops and VIP sale notices</label>
    <h2 class="section-title" style="left:34px;top:278px;font-size:18.5px;">Shipping Address</h2>
    <label class="check large" style="left:37px;top:313px;"><span class="box"></span>Billing address is same as shipping address</label>
  </section>

  <section class="panel panel-filter">
    <h2 class="section-title" style="left:35px;top:29px;font-size:23px;">Help us filter our emails so we are only sending relevant information to you.</h2>

    <h3 class="group-title" style="top:72px;font-weight:400;">Send me emails about these product types:</h3>
    <label class="check" style="left:44px;top:101px;"><span class="box"></span>Low energy motion loops</label>
    <label class="check" style="left:44px;top:126px;"><span class="box"></span>High energy motion loops</label>
    <label class="check" style="left:44px;top:151px;"><span class="box"></span>Timelapse footage</label>
    <label class="check" style="left:44px;top:176px;"><span class="box"></span>Worship or wedding motion loops</label>
    <label class="check" style="left:44px;top:201px;"><span class="box"></span>Pre-mixed DVDs and BluRay</label>
    <label class="check" style="left:341px;top:100px;"><span class="box"></span>Entertainment lasers for concerts and clubs</label>
    <label class="check" style="left:341px;top:125px;"><span class="box"></span>Entertainment lasers for text &amp; logo display</label>
    <label class="check" style="left:341px;top:150px;"><span class="box"></span>Custom logo animation services</label>
    <label class="check" style="left:341px;top:175px;"><span class="box"></span>Video software for creating video animations</label>
    <label class="check" style="left:341px;top:200px;"><span class="box"></span>Video software for live performance (Vjing)</label>

    <h3 class="group-title" style="top:243px;font-weight:400;">I am Involved in or have interest in:</h3>
    <label class="check" style="left:44px;top:272px;"><span class="box"></span>VJing (live performance video)</label>
    <label class="check" style="left:44px;top:297px;"><span class="box"></span>DJing (live performance audio+video)</label>
    <label class="check" style="left:44px;top:322px;"><span class="box"></span>Performing in a band</label>
    <label class="check" style="left:44px;top:347px;"><span class="box"></span>Video editing</label>
    <label class="check" style="left:44px;top:372px;"><span class="box"></span>Corporate presentations</label>
    <label class="check" style="left:341px;top:271px;"><span class="box"></span>Worship video services</label>
    <label class="check" style="left:341px;top:296px;"><span class="box"></span>Lasers for entertainment &amp; branding</label>
    <label class="check" style="left:341px;top:321px;"><span class="box"></span>Special offers from BrightVanta partners</label>
    <label class="check" style="left:341px;top:346px;"><span class="box"></span>Unsubscribe from all email lists</label>

    <button class="submit" type="button">Submit</button>
  </section>

  <footer class="footer">
    <p>All Rights Reserved Copyright© 2013 - BrightVanta</p>
  </footer>
</body>
</html>
```